Exciting new website for concierge aesthetic company

Simple, elegant, fresh design for female owned concierge aesthetic company, catering to both men and women ages 30-60. We would like a home page with an exciting catch phrase, a brief description of the company and a section to fill out an appointment request that includes a section for a referral. Please also have a book appointment link in the header of all pages that will link back to booking information form on home page. Separate pages to include:
- Services = 3 different services. Each service stating the name of the service and then providing a brief description. 3 services are "Private Session" for 1 client, "Group Session" for 2-5 clients, "Party" for 6+ clients. Will provide service descriptions text later. Item at bottom of page to allow description of how to "Host a Party".
- Products = 4 different product lines. Will provide pictures of product, brief description and link to manufacturer's website.
- Stories = brief client reviews to include before and after photos
- About us = Personal picture with brief description of owner's fun, exciting and family focussed lifestyle.
*Our domain is registered with varnix and we be using varnix for website hosting.

Target Market(s)

30-60 year old men and women, but mostly women

Industry/Entity Type

beauty and aesthetics

Coding

Coded - Design and coding required

Number of Pages Required

5+ page

Font styles to use
Sans Serif
Script

Colors
59FF00
82FF00
B8FF75
E3FFCB
F4FFEA
FFC000
F8CF3A
FAE287
FDF2CF
FEFAEE
F0912C
F2A743
F7CA91
FBE8D2
FDF5EE
E54698
E96AAD
F1A4CE
F9D9EA
FCEFF6

Requirements
Must have
• coded for varnix
Should not have
• corny pictures. No needles in pictures or graphics. No medical office or medical chair in pictures.

```html
<!DOCTYPE html>
<html lang="en">
<head>
<meta charset="utf-8">
<title>Glow Muse — Concierge Aesthetics</title>
<link rel="stylesheet" href="https://fonts.googleapis.com/css2?family=Dancing+Script:wght@400;500;600&family=Poppins:wght@400;500;600&display=block">
<style>
:root{
  --ink:#2b2b2b;
  --muted:#444;
  --coral:#f04a32;
  --pink:#ec2a6e;
  --pink-deep:#e0136a;
  --pink-hot:#ff3f73;
  --orange-a:#ff5a3c;
  --orange-b:#ff8a00;
  --paper:#ffffff;
  --mist:#f3f3f3;
  --field:#ffffff;
  --night:#262626;
  --script:'Dancing Script',cursive;
  --sans:'Poppins',sans-serif;
}
*{box-sizing:border-box;margin:0;padding:0}
html,body{width:1200px;height:4373px;overflow:hidden}
body{position:relative;background:var(--paper);font-family:var(--sans);color:var(--ink)}
h1,h2{font-weight:500}
.script{font-family:var(--script);font-weight:500}
.btn{position:absolute;display:flex;align-items:center;justify-content:center;border-radius:40px;color:#fff;
  background:linear-gradient(90deg,var(--pink-hot),var(--pink-deep));font-family:var(--script);font-weight:500;font-size:28px}

/* header */
.site-header{position:absolute;left:0;top:0;width:1200px;height:158px;background:#fff}
.brand{position:absolute;left:75px;top:60px;display:flex;align-items:center;gap:10px}
.brand-dot{width:22px;height:22px;border-radius:50%;background:var(--pink)}
.brand-name{font-family:var(--sans);font-weight:600;font-size:30px;color:var(--coral)}
.brand-tag{position:absolute;left:75px;top:132px;font-size:9px;letter-spacing:4px;color:var(--coral)}
.nav{position:absolute;top:64px;left:344px;display:flex;gap:41px;font-size:18px;color:var(--ink)}
.header-cta{left:879px;top:53px;width:246px;height:47px;font-family:var(--sans);font-weight:600;font-size:18px}

/* hero */
.hero{position:absolute;left:0;top:158px;width:1200px;height:640px;
  background:linear-gradient(90deg,#e8dcd2 0%,#ece7e4 40%,#e6e6e8 70%,#e2e2e4 100%)}
.hero-title{position:absolute;right:75px;top:225px;text-align:right;font-size:80px;line-height:88px;color:var(--pink)}
.hero-dots{position:absolute;left:570px;top:586px;display:flex;gap:8px}
.hero-dots span{width:9px;height:9px;border-radius:50%;background:#444}
.hero-dots span:first-child{background:var(--coral)}

/* split sections */
.split-title{position:absolute;left:75px;font-size:64px;line-height:80px;color:var(--coral)}
.split-copy{position:absolute;left:75px;width:520px;font-size:17px;line-height:36px;color:var(--muted)}
.split-photo{position:absolute;left:616px;width:509px;height:411px;border-radius:20px 0 90px 0}

/* services */
.services{position:absolute;left:0;top:1363px;width:1200px;height:585px;
  background:linear-gradient(90deg,var(--orange-a),var(--orange-b))}
.section-title{position:absolute;left:0;width:1200px;text-align:center;font-size:64px;line-height:80px}
.service{position:absolute;top:164px;width:327px;text-align:center;color:#fff}
.service-photo{height:263px;border-radius:0 0 70px 0}
.service-name{margin-top:14px;font-family:var(--script);font-weight:500;font-size:42px;line-height:50px}
.service-sub{font-size:16px;margin-top:4px}

/* products */
.product{position:absolute;top:2099px;width:243px;text-align:center}
.product-photo{height:229px}
.product-name{margin-top:18px;font-family:var(--script);font-weight:500;font-size:30px;color:var(--coral);line-height:34px}
.product-desc{font-size:16px;line-height:24px;color:var(--muted)}
.product-price{margin-top:16px;font-family:var(--script);font-weight:500;font-size:24px;color:var(--ink)}

/* booking */
.booking{position:absolute;left:0;top:2542px;width:1200px;height:699px;
  background:linear-gradient(90deg,var(--orange-a),var(--orange-b))}
.booking-photo{position:absolute;left:75px;top:80px;width:502px;height:411px;border-radius:0 90px 0 90px;
  background:linear-gradient(135deg,#d7d3cf,#b8aea6 55%,#8a7d72)}
.booking-card{position:absolute;left:526px;top:134px;width:599px;height:484px;background:var(--mist);
  border-radius:90px 0 90px 0;box-shadow:0 6px 20px rgba(0,0,0,.15)}
.booking-title{position:absolute;left:27px;top:18px;font-size:62px;line-height:76px;color:var(--coral)}
.field{position:absolute;width:263px;height:54px;border-radius:30px;background:var(--field);
  font-size:15px;color:#444;display:flex;align-items:center;justify-content:space-between;padding:0 26px}
.submit{left:27px;top:384px;width:542px;height:55px}

/* newsletter */
.loop{position:absolute;left:0;top:3820px;width:1200px;height:321px;background:#f4f4f4}
.loop-sub{position:absolute;left:0;top:147px;width:1200px;text-align:center;font-size:17px;color:var(--ink)}
.loop-input{position:absolute;left:300px;top:205px;width:396px;height:58px;border:1px solid #bbb;border-radius:30px;
  background:#fff;font-size:17px;padding-left:28px;display:flex;align-items:center}

/* footer */
.site-footer{position:absolute;left:0;top:4141px;width:1200px;height:232px;background:var(--night);color:#fff}
.footer-nav{position:absolute;top:54px;left:344px;display:flex;gap:41px;font-size:18px}
.copyright{position:absolute;top:104px;width:1200px;text-align:center;font-size:14px}
.social{position:absolute;top:140px;left:487px;display:flex;gap:28px}
.social span{width:26px;height:26px;border-radius:50%;background:#fff}
</style>
</head>
<body>

<header class="site-header">
  <div class="brand"><span class="brand-dot"></span><span class="brand-name">Glow Muse</span></div>
  <div class="brand-tag">CONCIERGE AESTHETICS</div>
  <nav class="nav"><span>Home</span><span>Services</span><span>Stories</span><span>About Us</span><span>Contact</span></nav>
  <div class="btn header-cta">Book Appointment</div>
</header>

<section class="hero" role="img" aria-label="Aesthetician gently treating a relaxed client's face in a bright studio">
  <h1 class="hero-title script">Redefining<br>Aesthetic Services</h1>
  <div class="hero-dots"><span></span><span></span><span></span><span></span></div>
</section>

<section class="about">
  <h2 class="split-title script" style="top:855px">About Glow Muse</h2>
  <p class="split-copy" style="top:946px">Sed ut perspiciatis unde omnis iste natus error sit voluptatem &nbsp;accusantium doloremque laudantium, totam rem aperiam, eaque ipsa quae ab illo inventore veritatis et quasi architecto beatae vitae dicta sunt explicaboemo enim ipsam voluptatem quia voluptas sit aspernatur aut odit aut fugit, sed quia consequuntur magni dolores eos qui ratione voluptatem sequi nesciunt.</p>
  <div class="btn" style="left:75px;top:1227px;width:197px;height:58px">Read More</div>
  <div class="split-photo" style="top:874px;background:linear-gradient(135deg,#e9d2c4,#d8b2a0 55%,#b98a78)" role="img" aria-label="Close-up of a woman's calm face with smooth skin"></div>
</section>

<section class="services">
  <h2 class="section-title script" style="top:60px;color:#fff">Our Services</h2>
  <div class="service" style="left:75px">
    <div class="service-photo" style="background:linear-gradient(135deg,#9fc3c8,#e2d4cb)" role="img" aria-label="One-on-one consultation with a client"></div>
    <div class="service-name">Private Session</div><div class="service-sub">For 1 Client</div>
  </div>
  <div class="service" style="left:438px">
    <div class="service-photo" style="background:linear-gradient(135deg,#c9c6c2,#6f6a66)" role="img" aria-label="Small group seated together in conversation"></div>
    <div class="service-name">Group Session</div><div class="service-sub">For 2-5 Clients</div>
  </div>
  <div class="service" style="left:799px">
    <div class="service-photo" style="background:linear-gradient(135deg,#e8e2da,#b9a591)" role="img" aria-label="Friends sharing food and drinks around a table"></div>
    <div class="service-name">Party</div><div class="service-sub">For 6+Clients</div>
  </div>
</section>

<section class="products">
  <h2 class="section-title script" style="top:1985px;color:var(--coral)">Our Products</h2>
  <div class="product" style="left:75px">
    <div class="product-photo" style="background:linear-gradient(135deg,#e6cbbb,#c9a08c)" role="img" aria-label="Skincare product application"></div>
    <div class="product-name">Product Name</div><div class="product-desc">Excepteur sint occaecat<br>cupidatat non</div><div class="product-price">$12.00</div>
  </div>
  <div class="product" style="left:345px">
    <div class="product-photo" style="background:linear-gradient(135deg,#ececec,#c7a996)" role="img" aria-label="Men's skincare product application"></div>
    <div class="product-name">Product Name</div><div class="product-desc">Excepteur sint occaecat<br>cupidatat non</div><div class="product-price">$12.00</div>
  </div>
  <div class="product" style="left:614px">
    <div class="product-photo" style="background:linear-gradient(135deg,#f0dcd4,#b7a0d8)" role="img" aria-label="Lip care product application"></div>
    <div class="product-name">Product Name</div><div class="product-desc">Excepteur sint occaecat<br>cupidatat non</div><div class="product-price">$12.00</div>
  </div>
  <div class="product" style="left:884px">
    <div class="product-photo" style="background:linear-gradient(135deg,#ecd9d2,#e3a7a7)" role="img" aria-label="Facial skincare product application"></div>
    <div class="product-name">Product Name</div><div class="product-desc">Excepteur sint occaecat<br>cupidatat non</div><div class="product-price">$12.00</div>
  </div>
</section>

<section class="booking" id="book">
  <div class="booking-photo" role="img" aria-label="Friendly reception desk where a client books an appointment"></div>
  <form class="booking-card">
    <h2 class="booking-title script">Book Appointment</h2>
    <div class="field" style="left:27px;top:116px">Name</div>
    <div class="field" style="left:306px;top:116px">Email Address</div>
    <div class="field" style="left:27px;top:182px">Phone No</div>
    <div class="field" style="left:306px;top:182px">Services Request
      <svg width="10" height="14" viewBox="0 0 10 14"><path d="M1 5l4-4 4 4M1 9l4 4 4-4" fill="#333"/></svg></div>
    <div class="field" style="left:27px;top:248px">Select Date
      <svg width="14" height="14" viewBox="0 0 14 14" fill="none" stroke="#333" stroke-width="1.4"><rect x="1" y="2.5" width="12" height="10.5" rx="1"/><path d="M1 6h12M4 1v3M10 1v3"/></svg></div>
    <div class="field" style="left:306px;top:248px">Select Time
      <svg width="15" height="15" viewBox="0 0 15 15" fill="none" stroke="#333" stroke-width="1.4"><circle cx="7.5" cy="7.5" r="6.3"/><path d="M7.5 4v4h3"/></svg></div>
    <div class="field" style="left:27px;top:314px">Reffered By</div>
    <div class="field" style="left:306px;top:314px">Interested in Hosting
      <svg width="10" height="14" viewBox="0 0 10 14"><path d="M1 5l4-4 4 4M1 9l4 4 4-4" fill="#333"/></svg></div>
    <div class="btn submit">Submit</div>
  </form>
</section>

<section class="host">
  <h2 class="split-title script" style="top:3312px">Host a Party</h2>
  <p class="split-copy" style="top:3401px">Sed ut perspiciatis unde omnis iste natus error sit voluptatem &nbsp;accusantium doloremque laudantium, totam rem aperiam, eaque ipsa quae ab illo inventore veritatis et quasi architecto beatae vitae dicta sunt explicaboemo enim ipsam voluptatem quia voluptas sit aspernatur aut odit aut fugit, sed quia consequuntur magni dolores eos qui ratione voluptatem sequi nesciunt.</p>
  <div class="btn" style="left:75px;top:3683px;width:197px;height:58px">Read More</div>
  <div class="split-photo" style="top:3330px;background:radial-gradient(circle at 50% 60%,#b86a3a,#5a2c1a 60%,#2a1510)" role="img" aria-label="Host serving dinner to friends at a warmly lit table"></div>
</section>

<section class="loop">
  <h2 class="section-title script" style="top:60px;color:var(--coral)">Stay in the Loop</h2>
  <p class="loop-sub">Get the latest when you sign up for our newsletter.</p>
  <div class="loop-input">Email Address</div>
  <div class="btn" style="left:706px;top:205px;width:197px;height:58px">Subscribe</div>
</section>

<footer class="site-footer">
  <nav class="footer-nav"><span>Home</span><span>Services</span><span>Stories</span><span>About Us</span><span>Contact</span></nav>
  <p class="copyright">©Copyright 2022 Company Name &nbsp;All Rights Reserved</p>
  <div class="social"><span></span><span></span><span></span><span></span><span></span></div>
</footer>

</body>
</html>
```